Biz Card

MARKETING today is the most rapidly changing business discipline. Media options to reach customers, actual customer preferences and consumer buying decisions change by the minute . . . no, by the second. The behavioral data generated by all aspects of the business and the new technologies that put the data to work together produce the potential to generate business intelligence and guide smart resource allocation to influence purchase and retention. However, to realize this potential, marketing professionals at all levels and in all organizations must continuously improve their skills not just from on-the-job training but by learning from masters in the field. The Bright Horizon Guild is the training center that serves this professional development need.model logos:msi.orgama.orgcontentmarketinginstitute.comBook covers on MarketingMetrics, Marketing Anaytics
Industry/Entity Type
Business
Contact Information for Business Card
Roy A. YoungCEOMarketing Science Academyphone: 310-601-4755email: roy@marketingscience.comAddress:437 South Rexford DriveBeverly Hills, CA 89377
Look and feel
Each slider illustrates characteristics of the customer's brand and the style your logo design should communicate.

```html
<!DOCTYPE html>
<html lang="en">
<head>
<meta charset="utf-8">
<title>Bright Horizon Guild – Business Card</title>
<link href="https://fonts.googleapis.com/css2?family=Questrial&family=Roboto:wght@400;700&display=swap" rel="stylesheet">
<style>
  :root {
    --backdrop: #a8a6a6;
    --brand-blue: #3b6a9a;
    --paper: #fbfbfb;
    --ink: #3f3f3f;
    --ink-soft: #4a4a4a;
    --white: #ffffff;
  }
  * { margin: 0; padding: 0; box-sizing: border-box; }
  html, body { width: 1200px; height: 1200px; overflow: hidden; }
  body { background: var(--backdrop); position: relative; font-family: "Roboto", Arial, sans-serif; }

  .card { position: absolute; width: 713px; height: 420px; }
  .card--front { left: 238px; top: 117px; background: var(--brand-blue); }
  .card--back { left: 230px; top: 643px; background: var(--paper); overflow: hidden; }

  .brand { position: absolute; display: flex; align-items: center; }
  .brand__mark { flex: none; }
  .brand__name {
    font-family: "Questrial", "Century Gothic", sans-serif;
    font-weight: 400;
  }
  .card--front .brand { left: 162px; top: 156px; gap: 52px; }
  .card--front .brand__mark { width: 76px; height: 76px; background: var(--white); }
  .card--front .brand__name { color: var(--white); font-size: 34px; line-height: 36px; }

  .card--back .brand { left: 62px; top: 176px; gap: 44px; }
  .card--back .brand__mark { width: 62px; height: 62px; background: var(--brand-blue); }
  .card--back .brand__name { color: var(--ink-soft); font-size: 25px; line-height: 25px; }

  .contact { position: absolute; left: 404px; top: 100px; color: var(--ink); }
  .contact__name { color: var(--brand-blue); font-weight: 700; font-size: 25px; letter-spacing: -0.2px; }
  .contact__title { font-size: 15px; margin-top: 10px; }
  .contact__address { font-size: 17px; line-height: 24px; margin-top: 28px; }
  .contact__list { list-style: none; margin-top: 5px; font-size: 17px; line-height: 24px; }
  .contact__list li { display: flex; align-items: center; gap: 21px; }
  .contact__icon { width: 15px; height: 15px; fill: var(--brand-blue); flex: none; margin-left: 1px; }

  .card__band { position: absolute; left: 0; bottom: 0; width: 100%; height: 17px; background: var(--brand-blue); }
</style>
</head>
<body>
  <section class="card card--front">
    <div class="brand">
      <span class="brand__mark"></span>
      <span class="brand__name">Bright<br>Horizon<br>Guild</span>
    </div>
  </section>

  <section class="card card--back">
    <div class="brand">
      <span class="brand__mark"></span>
      <span class="brand__name">Bright<br>Horizon<br>Guild</span>
    </div>

    <div class="contact">
      <h1 class="contact__name">Neil P. Barton</h1>
      <p class="contact__title">CEO</p>
      <p class="contact__address">912 North Calloway Lane<br>Beverly Hills, CA 89377</p>
      <ul class="contact__list">
        <li>
          <svg class="contact__icon" viewBox="0 0 16 16" aria-hidden="true"><path d="M1 5c0-2 3-3 7-3s7 1 7 3v1h-3V5H4v1H1z"/><path d="M4 7h8l2 7H2z"/><circle cx="8" cy="10.5" r="1.6" fill="#fbfbfb"/></svg>
          <span>310-555-0182</span>
        </li>
        <li>
          <svg class="contact__icon" viewBox="0 0 16 16" aria-hidden="true"><path d="M1 3h14v10H1z"/><path d="M1.5 3.5 8 9l6.5-5.5" fill="none" stroke="#fbfbfb" stroke-width="1.4"/></svg>
          <span>neil@brighthorizonguild.com</span>
        </li>
        <li>
          <svg class="contact__icon" viewBox="0 0 16 16" aria-hidden="true"><circle cx="8" cy="8" r="7"/><g fill="none" stroke="#fbfbfb" stroke-width="1"><ellipse cx="8" cy="8" rx="3" ry="7"/><path d="M1 8h14M2 4.5h12M2 11.5h12"/></g></svg>
          <span>www.brighthorizonguild.com</span>
        </li>
      </ul>
    </div>

    <div class="card__band"></div>
  </section>
</body>
</html>
```